Machinery Harbor Corp - Business Card Design

Need a new modern designed business card that is different and stands out to represent my equipment financing company. Machinery Harbor Corp finances all types of equipment and all types of industries. We like to do equipment financing a different way by putting customers first and want our card to represent that different approach to business. I want a card that some remembers when they receive it so it sticks in their mind and makes that wow impression.

Card should have a black background so the logo stands out. It can be horizontial or vertical or a combination of both.

Front of card information is below that shows the information that would go on my card. That is where I want a different look or design to stand out. The front could be split black/orange colour so the logo could pop on black side and information on orange side with different lettering. Just outside the box thinking on the front of the card. Open to any type of design.

Back of card is below which i I like unless you have a different spin to provide or a different idea that would make the card better as I am open to anything that looks great.

Target Market(s)

Machinery Harbor Corp deals with business owners in all industries.

Industry/Entity Type

Business

Contact Information for Business Card

Colors

Designer to choose colors to be used in the design.

Requirements
Must have
• Modern
• Different
• Stand Out
• Makes an Impression

```html
<!DOCTYPE html>
<html lang="en">
<head>
<meta charset="utf-8">
<title>Machinery Harbor Corp – Business Card</title>
<link rel="stylesheet" href="https://fonts.googleapis.com/css2?family=Lato:wght@400;700&display=swap">
<style>
  :root {
    --backdrop: #5b5b5b;
    --card: #000000;
    --ink: #ffffff;
    --accent: #ee6a1f;
  }
  * { box-sizing: border-box; margin: 0; padding: 0; }
  html, body {
    width: 1189px;
    height: 1200px;
    overflow: hidden;
    background: var(--backdrop);
    font-family: "Lato", sans-serif;
  }
  .card {
    position: absolute;
    left: 170px;
    width: 857px;
    height: 489px;
    background: var(--card);
    color: var(--ink);
  }
  .card--front { top: 67px; }
  .card--back { top: 625px; }

  .brand {
    position: absolute;
    display: flex;
    flex-direction: column;
    align-items: center;
    text-align: center;
  }
  .brand__mark {
    width: 140px;
    height: 140px;
    border-radius: 50%;
    background: var(--accent);
  }
  .brand__name {
    margin-top: 34px;
    font-weight: 400;
    text-transform: uppercase;
    line-height: 1;
  }
  .brand__line { display: block; }
  .brand__line--main { font-size: 42px; letter-spacing: 0.08em; }
  .brand__line--sub { font-size: 21px; letter-spacing: 0.3em; margin-top: 12px; }

  .card--front .brand {
    left: 0;
    right: 0;
    top: 124px;
  }
  .card--front .brand__name { color: var(--ink); }

  .card--back .brand {
    left: 62px;
    width: 320px;
    top: 126px;
  }
  .card--back .brand__mark { width: 128px; height: 128px; }
  .card--back .brand__name { color: var(--accent); margin-top: 36px; }
  .card--back .brand__line--main { font-size: 37px; }
  .card--back .brand__line--sub { font-size: 19px; margin-top: 10px; }

  .contact {
    position: absolute;
    left: 430px;
    width: 370px;
    top: 120px;
    text-align: center;
  }
  .contact__name {
    font-weight: 700;
    font-size: 31px;
    line-height: 1.1;
    text-transform: uppercase;
  }
  .contact__title {
    font-weight: 400;
    font-size: 23px;
    line-height: 1.25;
    text-transform: uppercase;
  }
  .contact__details {
    list-style: none;
    margin-top: 78px;
    font-size: 21px;
    line-height: 1.45;
  }
</style>
</head>
<body>
  <section class="card card--front" aria-label="Card front">
    <div class="brand">
      <span class="brand__mark" aria-hidden="true"></span>
      <p class="brand__name">
        <span class="brand__line brand__line--main">Machinery</span>
        <span class="brand__line brand__line--sub">Harbor Corp</span>
      </p>
    </div>
  </section>

  <section class="card card--back" aria-label="Card back">
    <div class="brand">
      <span class="brand__mark" aria-hidden="true"></span>
      <p class="brand__name">
        <span class="brand__line brand__line--main">Machinery</span>
        <span class="brand__line brand__line--sub">Harbor Corp</span>
      </p>
    </div>
    <div class="contact">
      <p class="contact__name">Dean Marlow</p>
      <p class="contact__title">President</p>
      <ul class="contact__details">
        <li>www.machineryharborcorp.ca</li>
        <li>403.555.0182</li>
        <li>dean@machineryharborcorp.ca</li>
      </ul>
    </div>
  </section>
</body>
</html>
```